Edgey, Modern Air Conditioning Website

Bramble Works
current website - www.kelvaroom.nz
Facebook - www.facebook.com/bramwrk

We really have no idea about webdesign etc we are Engineers not Graphic artists or creative writers. We really just want a edgy, modern website completed on our behalf

We can get pictures of projects as directed or happy for you to use stock images of Talvoro Mecha NZ (Heatpumps) air conditioning and exposed ducting etc

we would like the website to be heavily based on the below website. I like what they have done with both the site and the app but obviously would need to suit Bramble Works, snowflakes heating cooling etc etc Blue and white to match our logo etc

http://parrowbeams.co.nz/

Need links to contact page:
Bramble Works
27 Harlow Crescent
Petone
Wellington

0800 529 174 (0800BRAMWKS)

Marta.k@bramwks.co.nz

BRAMBLE WORKS
SATISFACTION GAURANTEED

WHY CHOOSE BRAMBLE WORKS
EXPERIENCE COUNTS

We have a team of nationally trained and qualified Refrigeration/HVAC/Electrical Engineers and Technicians based in Petone, Wellington offering services to Wellington, Manuwatu and the Wairarapa. We are factory trained and authorised to design, service and install all major brands including Talvoro, Pelnor, Korrowane Electric, Veltrada and Osmelo units. We extend our installation warranty to match that of the manufacturer’s warranty and specialise in our own diagnostics and repair.

SATISFACTION GUARANTEE
We aim to please and I put my name behind our brand! We will take care of your project from start to finish and offer a unique experience with our 100% satisfaction Guarantee*. We will supply and install your system and if your system is not installed how it was explained or not up to a trades standard we will return to make any the necessary modifications free of charge. We back this service up with our 0% upfront strategy, the power is in your hands. We will only invoice you once the installation has been completed up to a BRAMBLE WORKS standard.

LOW PRESSURE SALES
Nobody likes the vacuum salesmen’s techniques and neither do we. We will come to your home or business to provide a free measure and quote. Our experience will insure this is a quick and painless experience, you will be provided with expert advice from a qualified Refrigeration Engineer, not a car salesmen turned “Heating Guru”. We will follow up with an email providing our best price straight up, installation details and online brochures. We won’t bug you with repeated phone calls and inbox clogging emails. Once we receive confirmation we will issue you with an installation date and typically have your installation completed within 10 working days.

BRANDS
www.talvoromecha.co.nz
www.pelnor.co.nz
http://quellaro.co.nz/

SERVICES
Heatpumps/Air Conditioning – Heat pumps are the most efficient way of using electricity to heat your home, but some are more efficient than others. We will select the right model for your requirements taking into account the capacity required, the visual impact of the system, the style of system, air flow and obviously your personal preferences. We only install the highest quality brands that offer outstanding after sales support. Cassettes, Consoles, Under Ceilings, Ducted, Hiwalls, Multis… Confused? Give us a call.

COMMERCIAL
We have a growing Portfolio of clients that rely on us for their Commercial requirements. We have proven ourselves to be a force to be reckoned with to be able to think outside the square and come up with unique and cost effective solutions to heat and cool large areas.

CENTRAL HEATING
Ducted Heatpumps are the holy grail of central heating and guess what? They can also cool and dehumidify your home. Ducted Heatpumps are often overlooked or priced out of reach by less experienced salesmen as its not just a point and shoot approach. We pride ourselves in our work with Ducted systems, we are able to provide quick and economic quotations and can provide expert advice on all the extra options on Ducted systems with zone control, fresh air integration, positive pressure solutions. We use the best materials when it comes to insulated ducting, mounting equipment, drainage materials. Every system we design is designed with the lowest possible decibel reading, least amount of static pressure and maximum effieciency with the help of the very latest software available.

VENTILATION
Home ventilation is a very important part of insuring you have a nice dry home to maximise the efficiency of your Heat pump. Whilst HRV systems are not designed to Heat your house they are designed to keep it dry, provide fresh filtered air to ensure your home healthy and easy to heat. We offer a number of solutions from integrated ducted heatpump systems to balanced heat recovery systems and positive air systems.

TESTIMONIALS
http://www.lotbazaro.co.nz/Browse/Listing.aspx?id=415728306

Target Market(s)

Home Owners

Industry/Entity Type

Air Conditioning

Colors
33a6d7
ffffff

Requirements
Must have
• Could possibly use the 'O' from Bramble Works logo throughout website - see business Card
Nice to have
• Bright & Crisp - White and Blue
• Would love to have our Logo used throughout the website.

```html
<!DOCTYPE html>
<html lang="en">
<head>
<meta charset="utf-8">
<title>Bramble Works — Heating &amp; Air Conditioning</title>
<link href="https://fonts.googleapis.com/css2?family=Raleway:wght@400;500;600;700&family=Lato:wght@400;700&display=swap" rel="stylesheet">
<style>
:root{
  --blue:#33a6d7;
  --blue-deep:#1f93c8;
  --orange:#f4a417;
  --ink:#2b2b2b;
  --text:#555b61;
  --muted:#8a9096;
  --light:#f0f0f0;
  --line:#e3e3e3;
  --white:#ffffff;
  --black:#0d0d0d;
}
*{box-sizing:border-box;margin:0;padding:0}
html,body{width:1200px;height:3120px;overflow:hidden}
body{font-family:'Lato',sans-serif;color:var(--text);background:var(--white);font-size:13px;position:relative}
section,header,footer{position:relative;width:1200px;overflow:hidden}
h2.heading{font-family:'Raleway',sans-serif;font-weight:500;font-size:29px;color:var(--ink);letter-spacing:.5px;display:flex;align-items:center;gap:12px;white-space:nowrap}
h2.heading b{font-weight:700;color:var(--blue)}
.badge{width:28px;height:28px;border-radius:50%;border:4px solid #9aa3aa;flex:none}
.btn{display:inline-block;font-family:'Lato',sans-serif;font-size:13px;color:var(--white);padding:0 16px;height:36px;line-height:36px;border-radius:2px}
.btn.blue{background:var(--blue)}
.btn.orange{background:var(--orange)}

/* top bar */
.topbar{height:30px;background:var(--blue);color:var(--white);font-size:12px}
.topbar .addr{position:absolute;left:160px;top:8px;display:flex;align-items:center;gap:6px}
.topbar .social{position:absolute;right:160px;top:0;display:flex}
.topbar .social span{width:30px;height:30px;display:flex;align-items:center;justify-content:center;border-left:1px solid rgba(255,255,255,.25)}
.topbar .social span i{width:10px;height:10px;border-radius:50%;background:var(--white);display:block}

/* header */
.site-header{height:95px;background:var(--white)}
.logo{position:absolute;left:162px;top:24px;display:flex;align-items:center;gap:10px;font-family:'Raleway',sans-serif;font-weight:700;font-size:20px;line-height:22px;color:var(--blue);letter-spacing:1px}
.logo i{width:12px;height:12px;border-radius:50%;background:var(--blue);display:block;flex:none}
.nav{position:absolute;left:390px;top:42px;display:flex;gap:34px;font-family:'Raleway',sans-serif;font-size:11px;font-weight:500;color:#444}
.nav .active{color:var(--blue)}
.call{position:absolute;right:160px;top:26px;text-align:right}
.call small{font-size:14px;color:#666;display:block}
.call strong{font-family:'Raleway',sans-serif;font-weight:500;font-size:21px;color:var(--blue);display:flex;align-items:center;gap:8px;justify-content:flex-end}

/* hero */
.hero{height:480px;background:linear-gradient(100deg,#6f777e 0%,#858c92 30%,#a9aeb2 50%,#dfe2e4 75%,#eceef0 100%)}
.hero .photo{position:absolute;inset:0}
.hero .copy{position:absolute;left:165px;top:162px;color:var(--white)}
.hero h1{font-family:'Raleway',sans-serif;font-weight:700;font-size:32px;letter-spacing:.5px;text-shadow:0 1px 4px rgba(0,0,0,.35)}
.hero p{font-family:'Raleway',sans-serif;font-size:25px;line-height:32px;margin-top:6px;text-shadow:0 1px 4px rgba(0,0,0,.35)}
.hero .actions{position:absolute;left:165px;top:280px;display:flex;gap:12px}
.dots{position:absolute;left:570px;top:442px;display:flex;gap:5px}
.dots i{width:12px;height:12px;border-radius:50%;border:2px solid var(--blue);display:block;background:var(--white)}
.dots i.on{background:var(--orange);border-color:var(--orange);width:15px;height:15px;margin-top:-1px}
.hero .rule{position:absolute;left:0;bottom:0;width:100%;height:8px;background:var(--blue)}

/* about */
.about{height:425px}
.about .intro{position:absolute;left:162px;top:40px;width:460px}
.about .sub{font-family:'Raleway',sans-serif;font-size:14px;color:#555;margin-top:10px}
.about .lead{font-size:11px;line-height:16px;color:var(--text);margin-top:18px}
.about ul{list-style:none;margin-top:14px}
.about li{font-size:13px;color:#444;line-height:24px;display:flex;align-items:center;gap:16px}
.about .actions{display:flex;gap:12px;margin-top:22px}
.about .photo{position:absolute;left:655px;top:56px;width:385px;height:318px;padding:6px;border:1px solid var(--line);background:var(--white)}
.about .photo div{width:100%;height:100%;background:linear-gradient(160deg,#4b4a48 0%,#8a847c 45%,#c9c2b6 75%,#6d8ba0 100%)}

/* services */
.services{height:615px;background:var(--blue);color:var(--white)}
.services h2.heading{color:var(--white);justify-content:center;position:absolute;top:38px;width:1200px;font-size:27px}
.services h2.heading b{color:var(--white)}
.services h2 .badge{border-color:rgba(255,255,255,.8)}
.services .intro{position:absolute;left:160px;top:92px;width:880px;text-align:center;font-size:10.5px;line-height:15px}
.card{position:absolute;top:173px;width:233px;height:353px}
.card svg.frame{position:absolute;left:0;top:0}
.card h3{position:absolute;top:182px;width:100%;text-align:center;font-family:'Raleway',sans-serif;font-weight:500;font-size:19px}
.card p{position:absolute;top:214px;left:30px;width:173px;text-align:center;font-size:10.5px;line-height:15px}
.card .btn{position:absolute;top:310px;left:58px;height:34px;line-height:34px;width:117px;text-align:center;padding:0}
.card .icon{position:absolute;left:58px;top:34px}
.services .callout{position:absolute;top:572px;width:1200px;text-align:center;font-family:'Raleway',sans-serif;font-weight:500;font-size:22px;letter-spacing:.5px}

/* why */
.why{height:360px;background:var(--light)}
.why h2.heading{position:absolute;top:30px;width:1200px;justify-content:center}
.reason{position:absolute;top:108px;width:220px;text-align:center}
.reason .art{width:110px;height:110px;border-radius:50%;margin:0 auto;background:radial-gradient(circle,#f6b83a 0 30%,#2f2f2f 31% 55%,#e5e5e5 56%)}
.reason h3{font-family:'Raleway',sans-serif;font-weight:700;font-size:14px;color:var(--ink);line-height:18px;margin-top:26px}
.reason p{font-size:11px;line-height:16px;margin-top:8px;color:var(--text)}
.why .link{position:absolute;top:158px;height:2px;width:150px;background:#d4d4d4}

/* areas */
.areas{height:250px}
.areas .area-info{position:absolute;left:162px;top:40px;width:340px}
.areas h2.heading{font-size:27px}
.areas .place{display:flex;gap:10px;margin-top:20px}
.areas .place strong{font-family:'Raleway',sans-serif;color:var(--orange);font-size:14px;font-weight:700;display:block}
.areas .place span{font-size:14px;color:#555}
.areas hr{border:0;border-top:1px solid var(--line);margin:14px 0 12px;width:290px}
.areas .list{font-size:13px;line-height:18px;color:#555}
.areas .map{position:absolute;left:540px;top:20px;width:500px;height:215px;background:linear-gradient(90deg,#fdf6e8,#f3f3f3 60%,#fafafa);border-radius:4px}
.areas .pin{position:absolute;left:540px;top:115px;background:var(--blue);color:var(--white);font-size:11px;padding:4px 10px;border-radius:2px}

/* testimonials */
.testimonials{height:335px;background:linear-gradient(180deg,#e9e9e9,#f2f2f2)}
.testimonials h2.heading{position:absolute;top:40px;width:1200px;justify-content:center}
.quote{position:absolute;top:104px;width:277px;height:180px;background:var(--white);padding:22px 24px}
.quote p{font-size:11px;line-height:17px;color:#333}
.quote .who{position:absolute;left:24px;top:98px;display:flex;gap:14px;align-items:center}
.quote .avatar{width:62px;height:62px;border-radius:50%;border:3px solid var(--blue);background:linear-gradient(180deg,#cdd3d8,#8f979e)}
.quote .who strong{font-size:13px;color:#222;display:block}
.quote .who strong.hl{color:var(--orange)}
.quote .who span{font-size:11px;color:#666}

/* contact */
.contact{height:245px}
.contact .title{position:absolute;left:162px;top:48px;display:flex;gap:10px}
.contact .title h2{font-family:'Raleway',sans-serif;font-weight:500;font-size:21px;line-height:24px;color:var(--ink);letter-spacing:1px}
.contact .title h2 b{color:var(--blue);font-weight:700}
.contact .blurb{position:absolute;left:162px;top:120px;width:280px;font-size:11px;line-height:17px;color:#444}
.contact .form{position:absolute;left:476px;top:48px;width:564px}
.contact .form h3{font-size:13px;font-weight:400;color:#333}
.fields{display:grid;grid-template-columns:1fr 1fr;gap:10px 22px;margin-top:14px}
.field{height:34px;border:1px solid #d7d7d7;font-size:10px;color:#999;padding:11px 12px}
.contact .btn{margin-top:14px;height:34px;line-height:34px;padding:0 22px}

/* footer */
.site-footer{height:230px;background:var(--black);color:var(--white)}
.site-footer h4{font-family:'Raleway',sans-serif;font-weight:500;font-size:17px;letter-spacing:1px}
.site-footer h4 b{font-weight:700}
.links{position:absolute;left:162px;top:38px}
.links ul{list-style:none;margin-top:18px}
.links li{font-size:12px;line-height:23px;display:flex;align-items:center;gap:12px}
.contact-info{position:absolute;left:378px;top:38px}
.contact-info .row{display:flex;gap:12px;font-size:12px;line-height:16px;margin-top:16px}
.contact-info .row.first{margin-top:20px}
.fmap{position:absolute;left:650px;top:45px;width:390px;height:125px;background:linear-gradient(120deg,#e8e6e0,#f2efe8 55%,#cfe1ee);border-radius:3px}
.site-footer .view{position:absolute;left:652px;top:182px;font-size:12px;color:#999}
.bottombar{position:relative;height:55px;background:var(--blue);color:var(--white);font-size:11px}
.bottombar .follow{position:absolute;left:162px;top:15px;display:flex;gap:8px;align-items:center}
.bottombar .follow i{width:26px;height:26px;border-radius:50%;border:2px solid var(--white);display:block}
.bottombar .follow span{margin-right:8px}
.bottombar .copy{position:absolute;right:160px;top:21px}
</style>
</head>
<body>

<div class="topbar">
  <div class="addr">
    <svg width="10" height="13" viewBox="0 0 10 13"><path d="M5 0a5 5 0 0 0-5 5c0 3.5 5 8 5 8s5-4.5 5-8a5 5 0 0 0-5-5zm0 7a2 2 0 1 1 0-4 2 2 0 0 1 0 4z" fill="#fff"/></svg>
    27 Harlow Crescent, Petone, Wellington
  </div>
  <div class="social"><span><i></i></span><span><i></i></span><span><i></i></span><span><i></i></span></div>
</div>

<header class="site-header">
  <div class="logo"><i></i><span>BRAMBLE<br>WORKS</span></div>
  <nav class="nav"><span class="active">HOME</span><span>ABOUT US</span><span>SERVICES</span><span>TESTIMONIALS</span><span>CONTACT US</span></nav>
  <div class="call">
    <small>Any Query? Call us now</small>
    <strong><svg width="16" height="16" viewBox="0 0 24 24"><path d="M6.6 10.8a15.1 15.1 0 0 0 6.6 6.6l2.2-2.2a1 1 0 0 1 1-.25 11.4 11.4 0 0 0 3.6.57 1 1 0 0 1 1 1V20a1 1 0 0 1-1 1A17 17 0 0 1 3 4a1 1 0 0 1 1-1h3.5a1 1 0 0 1 1 1c0 1.25.2 2.45.57 3.57a1 1 0 0 1-.25 1z" fill="#33a6d7"/></svg>022 418 3906</strong>
  </div>
</header>

<section class="hero">
  <div class="photo" role="img" aria-label="Technician in work overalls servicing a wall-mounted heat pump unit"></div>
  <div class="copy">
    <h1>SPECIALIZING IN</h1>
    <p>Commercial And<br>Central Heating System</p>
  </div>
  <div class="actions"><span class="btn blue">Read More</span><span class="btn orange">Contact Now</span></div>
  <div class="dots"><i></i><i class="on"></i><i></i></div>
  <div class="rule"></div>
</section>

<section class="about">
  <div class="intro">
    <h2 class="heading"><span class="badge"></span><span>ABOUT <b>KELVA ROOM</b></span></h2>
    <p class="sub">SPECIALIZING IN Commercial And Central Heating System</p>
    <p class="lead">Lorem ipsum dolor sit amet, consectetuer adipiscing elit, sed diam nonummy nibh euismod tincidunt ut laoreet dolore magna aliquam erat volutpat. Ut wisi enim ad minim veniam, quis nostrud exerci tation ullamcorper suscipit lobortis.</p>
    <ul>
      <li><svg width="14" height="8" viewBox="0 0 14 8"><path d="M0 4h12M9 1l3 3-3 3" stroke="#33a6d7" stroke-width="1.5" fill="none"/></svg>Lorem ipsum dolor sit amet, consectetur adipiscing elit.</li>
      <li><svg width="14" height="8" viewBox="0 0 14 8"><path d="M0 4h12M9 1l3 3-3 3" stroke="#33a6d7" stroke-width="1.5" fill="none"/></svg>Aenean luctus odio congue congue viverra.</li>
      <li><svg width="14" height="8" viewBox="0 0 14 8"><path d="M0 4h12M9 1l3 3-3 3" stroke="#33a6d7" stroke-width="1.5" fill="none"/></svg>Curabitur tempor magna sed arcu finibus, sed interdum risus hendrerit.</li>
      <li><svg width="14" height="8" viewBox="0 0 14 8"><path d="M0 4h12M9 1l3 3-3 3" stroke="#33a6d7" stroke-width="1.5" fill="none"/></svg>Maecenas vulputate elit eleifend tristique pharetra.</li>
      <li><svg width="14" height="8" viewBox="0 0 14 8"><path d="M0 4h12M9 1l3 3-3 3" stroke="#33a6d7" stroke-width="1.5" fill="none"/></svg>Mauris in ante quis tellus pulvinar dignissim.</li>
    </ul>
    <div class="actions"><span class="btn blue">Read More</span><span class="btn orange">Contact Now</span></div>
  </div>
  <div class="photo"><div role="img" aria-label="Modern living room with exposed ceiling beams, brick wall and leather sofas"></div></div>
</section>

<section class="services">
  <h2 class="heading"><span class="badge"></span><span>OUR <b>SERVICES</b></span></h2>
  <p class="intro">Heatpumps/Air Conditioning – Heat pumps are the most efficient way of using electricity to heat your home, but some are more efficient than others. We will select the right model for your requirements taking into account the capacity required, the visual impact of the system, the style of system, air flow and obviously your personal preferences. We only install the highest quality brands that offer outstanding after sales support. Cassettes, Consoles, Under Ceilings, Ducted, Hiwalls, Multis...</p>

  <div class="card" style="left:204px">
    <svg class="frame" width="233" height="353" viewBox="0 0 233 353"><path d="M1 352V112L60 60M173 60L232 112V352H1" fill="none" stroke="#fff" stroke-width="1.5"/><circle cx="116.5" cy="62" r="60" fill="#fff"/><circle cx="116.5" cy="62" r="52" fill="none" stroke="#33a6d7" stroke-width="2"/></svg>
    <svg class="icon" width="117" height="58" viewBox="0 0 117 58"><rect x="36" y="12" width="45" height="16" rx="3" fill="none" stroke="#33a6d7" stroke-width="2.5"/><path d="M42 22h33M48 34c-3 4-3 8 0 12M58.5 34v12M69 34c3 4 3 8 0 12" stroke="#33a6d7" stroke-width="2.5" fill="none"/></svg>
    <h3>COMMERCIAL</h3>
    <p>We have a growing Portfolio of clients that rely on us for their Commercial requirements. We have proven ourselves to be a force to be reckoned with to be able...</p>
    <span class="btn orange">Read More</span>
  </div>
  <div class="card" style="left:483px">
    <svg class="frame" width="233" height="353" viewBox="0 0 233 353"><path d="M1 352V112L60 60M173 60L232 112V352H1" fill="none" stroke="#fff" stroke-width="1.5"/><circle cx="116.5" cy="62" r="60" fill="#fff"/><circle cx="116.5" cy="62" r="52" fill="none" stroke="#33a6d7" stroke-width="2"/></svg>
    <svg class="icon" width="117" height="58" viewBox="0 0 117 58"><path d="M46 8c-2 2 2 4 0 6M53 8c-2 2 2 4 0 6M60 8c-2 2 2 4 0 6M67 8c-2 2 2 4 0 6M74 8c-2 2 2 4 0 6" stroke="#33a6d7" stroke-width="2" fill="none"/><rect x="40" y="18" width="38" height="26" rx="2" fill="none" stroke="#33a6d7" stroke-width="2.5"/><path d="M47 18v26M54 18v26M61 18v26M68 18v26M43 44v5M75 44v5" stroke="#33a6d7" stroke-width="2"/></svg>
    <h3>CENTRAL HEATING</h3>
    <p>Ducted Heatpumps are the holy grail of central heating and guess what? They can also cool and dehumidify your home. Ducted Heatpumps are often overlooked...</p>
    <span class="btn orange">Read More</span>
  </div>
  <div class="card" style="left:762px">
    <svg class="frame" width="233" height="353" viewBox="0 0 233 353"><path d="M1 352V112L60 60M173 60L232 112V352H1" fill="none" stroke="#fff" stroke-width="1.5"/><circle cx="116.5" cy="62" r="60" fill="#fff"/><circle cx="116.5" cy="62" r="52" fill="none" stroke="#33a6d7" stroke-width="2"/></svg>
    <svg class="icon" width="117" height="58" viewBox="0 0 117 58"><g fill="#33a6d7" transform="translate(58.5 28)"><circle r="4"/><path d="M0-4C-4-10-2-20 6-20 10-14 6-8 0-4z"/><path d="M0-4C-4-10-2-20 6-20 10-14 6-8 0-4z" transform="rotate(120)"/><path d="M0-4C-4-10-2-20 6-20 10-14 6-8 0-4z" transform="rotate(240)"/></g></svg>
    <h3>VENTILATION</h3>
    <p>Home ventilation is a very important part of insuring you have a nice dry home to maximise the efficiency of your Heat pump. Whilst HRV systems are not designed...</p>
    <span class="btn orange">Read More</span>
  </div>

  <div class="callout">CONFUSED? GIVE US A CALL - 022 418 3906</div>
</section>

<section class="why">
  <h2 class="heading"><span class="badge"></span><span>WHY CHOOSE <b>BRAMBLE WORKS</b></span></h2>
  <div class="link" style="left:373px"></div>
  <div class="link" style="left:664px"></div>
  <div class="reason" style="left:188px"><div class="art" role="img" aria-label="Isometric toolbox illustration"></div><h3>EXPERIENCE<br>COUNTS</h3><p>We have a team of nationally<br>trained and qualified. [+]</p></div>
  <div class="reason" style="left:479px"><div class="art" role="img" aria-label="Guarantee shield illustration"></div><h3>SATISFACTION<br>GUARANTEE</h3><p>We aim to please and I put my name<br>behind our brand! [+]</p></div>
  <div class="reason" style="left:770px"><div class="art" role="img" aria-label="Snowflake with pressure arrows illustration"></div><h3>LOW PRESSURE<br>SALES</h3><p>We aim to please and I put my name<br>behind our brand! [+]</p></div>
</section>

<section class="areas">
  <div class="area-info">
    <h2 class="heading"><span class="badge"></span><span>AREAS WE <b>SERVICED</b></span></h2>
    <div class="place">
      <svg width="14" height="20" viewBox="0 0 10 13"><path d="M5 0a5 5 0 0 0-5 5c0 3.5 5 8 5 8s5-4.5 5-8a5 5 0 0 0-5-5zm0 7a2 2 0 1 1 0-4 2 2 0 0 1 0 4z" fill="#8a9096"/></svg>
      <div><strong>WELLINGTON</strong><span>27 Harlow Crescent, Petone, Wellington</span></div>
    </div>
    <hr>
    <p class="list">Wellington, Masterton,<br>Palmerston North, Wanganui and<br>anywhere in between.</p>
  </div>
  <div class="map" role="img" aria-label="Outline map of the lower North Island with the Wellington service region highlighted"></div>
  <div class="pin">WELLINGTON</div>
</section>

<section class="testimonials" role="region" aria-label="Client testimonials">
  <h2 class="heading"><span class="badge"></span><span>CLIENTS <b>TESTIMONIALS</b></span></h2>
  <div class="quote" style="left:162px"><p>Lorem ipsum dolor sit amet, consectetuer adipiscing elit, sed diam nonummy nibh euismod tincidunt ut laoreet dolore .</p><div class="who"><div class="avatar" role="img" aria-label="Client portrait"></div><div><strong>Lewis Harrow</strong><span>Lorem ipsum</span></div></div></div>
  <div class="quote" style="left:462px"><p>Lorem ipsum dolor sit amet, consectetuer adipiscing elit, sed diam nonummy nibh euismod tincidunt ut laoreet dolore .</p><div class="who"><div class="avatar" role="img" aria-label="Client portrait"></div><div><strong class="hl">Lewis Harrow</strong><span>Lorem ipsum</span></div></div></div>
  <div class="quote" style="left:762px"><p>Lorem ipsum dolor sit amet, consectetuer adipiscing elit, sed diam nonummy nibh euismod tincidunt ut laoreet dolore .</p><div class="who"><div class="avatar" role="img" aria-label="Client portrait"></div><div><strong>Lewis Harrow</strong><span>Lorem ipsum</span></div></div></div>
</section>

<section class="contact">
  <div class="title"><span class="badge"></span><h2>QUICK<br><b>CONTACT</b></h2></div>
  <p class="blurb">Duis autem vel eum iriure dolor in hendrerit in vulputate velit esse molestie consequat, vel illum dolore eu feugiat nulla.</p>
  <div class="form">
    <h3>Please fill up bellow form</h3>
    <div class="fields"><div class="field">Name</div><div class="field">Email</div><div class="field">Phone</div><div class="field">Message</div></div>
    <span class="btn blue">Read More</span>
  </div>
</section>

<footer class="site-footer">
  <div class="links">
    <h4>QUICK <b>LINKS</b></h4>
    <ul>
      <li><svg width="5" height="8" viewBox="0 0 5 8"><path d="M1 1l3 3-3 3" stroke="#fff" fill="none"/></svg>Home</li>
      <li><svg width="5" height="8" viewBox="0 0 5 8"><path d="M1 1l3 3-3 3" stroke="#fff" fill="none"/></svg>About Us</li>
      <li><svg width="5" height="8" viewBox="0 0 5 8"><path d="M1 1l3 3-3 3" stroke="#fff" fill="none"/></svg>Services</li>
      <li><svg width="5" height="8" viewBox="0 0 5 8"><path d="M1 1l3 3-3 3" stroke="#fff" fill="none"/></svg>Testimonials</li>
      <li><svg width="5" height="8" viewBox="0 0 5 8"><path d="M1 1l3 3-3 3" stroke="#fff" fill="none"/></svg>Contact Us</li>
    </ul>
  </div>
  <div class="contact-info">
    <h4>CONTACT <b>INFO</b></h4>
    <div class="row first"><svg width="12" height="16" viewBox="0 0 10 13"><path d="M5 0a5 5 0 0 0-5 5c0 3.5 5 8 5 8s5-4.5 5-8a5 5 0 0 0-5-5zm0 7a2 2 0 1 1 0-4 2 2 0 0 1 0 4z" fill="#fff"/></svg><div>KELVAROOM<br>27 Harlow Crescent, Petone,<br>Wellington</div></div>
    <div class="row"><svg width="12" height="12" viewBox="0 0 24 24"><path d="M6.6 10.8a15.1 15.1 0 0 0 6.6 6.6l2.2-2.2a1 1 0 0 1 1-.25 11.4 11.4 0 0 0 3.6.57 1 1 0 0 1 1 1V20a1 1 0 0 1-1 1A17 17 0 0 1 3 4a1 1 0 0 1 1-1h3.5a1 1 0 0 1 1 1c0 1.25.2 2.45.57 3.57a1 1 0 0 1-.25 1z" fill="#fff"/></svg><div>022 418 3906</div></div>
    <div class="row"><svg width="13" height="10" viewBox="0 0 13 10"><rect width="13" height="10" rx="1" fill="#fff"/><path d="M0 1l6.5 5L13 1" stroke="#0d0d0d" fill="none"/></svg><div>Marta.k@bramwks.co.nz</div></div>
  </div>
  <div class="fmap" role="img" aria-label="Street map showing the Petone office location"></div>
  <span class="view">View Map</span>
</footer>

<div class="bottombar">
  <div class="follow"><span>Follow Us</span><i></i><i></i><i></i><i></i></div>
  <div class="copy">Copyright © 2016 Bramble Works. All Rights Reserved</div>
</div>

</body>
</html>
```